Business card for medical clinic

I need an upmarket, modern medical/health business card for my clinic

Contact Information for Business Card

name, address, email, qr code

```html
<!DOCTYPE html>
<html lang="en">
<head>
<meta charset="utf-8">
<title>Alderwell Health Clinic – Business Card</title>
<link href="https://fonts.googleapis.com/css2?family=Montserrat:wght@400;500;700&display=swap" rel="stylesheet">
<style>
  :root{
    --page:#e9ebee;
    --card:#ffffff;
    --navy:#133a5e;
    --blue-deep:#11527c;
    --blue-mid:#1a6f9e;
    --blue-light:#2399cc;
    --text-light:#ffffff;
    --shadow:rgba(10,30,50,.18);
  }
  *{box-sizing:border-box;margin:0;padding:0}
  html,body{width:1200px;height:880px;overflow:hidden}
  body{background:var(--page);font-family:'Montserrat',sans-serif;position:relative}

  .card{
    position:absolute;width:680px;height:388px;border-radius:34px;
    background:var(--card);overflow:hidden;
    box-shadow:0 14px 34px var(--shadow);
  }
  .card--front{left:60px;top:50px}
  .card--back{left:460px;top:442px}

  /* brand lockup */
  .brand{position:absolute;display:flex;align-items:center}
  .brand__dot{border-radius:50%;border:solid var(--blue-mid)}
  .brand__name{font-weight:500;color:var(--blue-mid);letter-spacing:.06em;text-transform:uppercase;line-height:1}
  .card--front .brand{left:0;right:0;top:0;bottom:0;justify-content:center;gap:22px}
  .card--front .brand__dot{width:70px;height:70px;border-width:6px}
  .card--front .brand__name{font-size:34px}
  .card--back .brand{right:46px;top:70px;gap:14px}
  .card--back .brand__dot{width:40px;height:40px;border-width:4px}
  .card--back .brand__name{font-size:19px}

  /* back side */
  .back__art{position:absolute;inset:0;width:100%;height:100%}
  .contact{position:absolute;left:46px;bottom:34px;color:var(--text-light)}
  .contact__name{font-weight:700;font-size:23px;letter-spacing:.04em;text-transform:uppercase}
  .contact__role{font-size:14px;margin-top:2px}
  .contact__address{font-size:14px;line-height:1.45;margin-top:22px}
  .contact__list{list-style:none;margin-top:20px;font-size:14px;line-height:1.6}
  .contact__list li{display:flex;align-items:center;gap:9px}
  .contact__icon{width:13px;height:13px;flex:none}
</style>
</head>
<body>

<section class="card card--front" aria-label="Card front">
  <div class="brand">
    <span class="brand__dot"></span>
    <span class="brand__name">Alderwell Health Clinic</span>
  </div>
</section>

<section class="card card--back" aria-label="Card back">
  <svg class="back__art" viewBox="0 0 680 388" preserveAspectRatio="none" aria-hidden="true">
    <defs>
      <linearGradient id="panelGradient" x1="0" y1="0" x2="1" y2="1">
        <stop offset="0" stop-color="#114d78"/>
        <stop offset=".5" stop-color="#17699a"/>
        <stop offset="1" stop-color="#2399cc"/>
      </linearGradient>
    </defs>
    <polygon points="0,0 136,0 530,388 0,388" fill="url(#panelGradient)"/>
    <polygon points="148,0 168,0 560,370 548,370" fill="#14557f"/>
  </svg>

  <div class="brand">
    <span class="brand__dot"></span>
    <span class="brand__name">Alderwell Health Clinic</span>
  </div>

  <div class="contact">
    <p class="contact__name">Daniel Reeve</p>
    <p class="contact__role">Managing Director</p>
    <p class="contact__address">Your address, City<br>State, Zip 1234</p>
    <ul class="contact__list">
      <li>
        <svg class="contact__icon" viewBox="0 0 24 24" aria-hidden="true"><path fill="#fff" d="M6.6 10.8a15 15 0 0 0 6.6 6.6l2.2-2.2c.3-.3.7-.4 1-.2 1.1.4 2.3.6 3.6.6.6 0 1 .4 1 1V20c0 .6-.4 1-1 1A17 17 0 0 1 3 4c0-.6.4-1 1-1h3.5c.6 0 1 .4 1 1 0 1.3.2 2.5.6 3.6.1.3 0 .7-.2 1z"/></svg>
        123 456 789
      </li>
      <li>
        <svg class="contact__icon" viewBox="0 0 24 24" aria-hidden="true"><rect x="2" y="5" width="20" height="14" rx="2" fill="#fff"/><path d="M3 6l9 7 9-7" fill="none" stroke="#1a6f9e" stroke-width="2"/></svg>
        info@yourmail.com
      </li>
      <li>
        <svg class="contact__icon" viewBox="0 0 24 24" aria-hidden="true"><circle cx="12" cy="12" r="10" fill="#fff"/><path d="M2 12h20M12 2c3 3 3 17 0 20M12 2c-3 3-3 17 0 20" fill="none" stroke="#1a6f9e" stroke-width="1.5"/></svg>
        www.yourwebsite.com
      </li>
    </ul>
  </div>
</section>

</body>
</html>
```